Redesign of Form/Document Navigation Page

I need a redesign of our document and navigation bar on the left. We want the same navigation bar layout/setup but want the buttons and typography to be simple and matching all over. The form needs to be aesthetically pleasing and fit within the page.

1st attachment is our Direct Deposit and the second is the form continued.

```html
<!DOCTYPE html>
<html lang="en">
<head>
<meta charset="utf-8">
<title>Direct Deposit – Sentinel Watch Services</title>
<link href="https://fonts.googleapis.com/css2?family=Open+Sans:wght@400;600;700&display=swap" rel="stylesheet">
<style>
:root{
  --navy:#1b1f6e;
  --gold:#f2ae1c;
  --page:#f3f3f3;
  --white:#ffffff;
  --line:#dcdcdc;
  --field:#e0e0e0;
  --field-border:#cfcfcf;
  --text:#333333;
  --muted:#666666;
}
*{box-sizing:border-box;margin:0;padding:0}
html,body{width:1200px;height:949px;overflow:hidden}
body{background:var(--page);font-family:"Open Sans",Arial,sans-serif;color:var(--text);position:relative}
.site-header{position:absolute;left:0;top:0;width:1200px;height:106px;background:var(--white);border-bottom:1px solid var(--line);box-shadow:0 1px 3px rgba(0,0,0,.06)}
.brand{position:absolute;left:132px;top:24px;display:flex;align-items:center;gap:10px}
.brand-mark{width:44px;height:44px;border-radius:50%;background:var(--navy)}
.brand-name{color:var(--gold);font-weight:700;font-size:21px;line-height:22px;letter-spacing:.2px}
.main-nav{position:absolute;left:638px;top:47px;display:flex;gap:26px;font-size:12px;color:var(--navy)}
.main-nav .sep{color:var(--text)}
.main-nav .help{color:var(--text)}
.user{position:absolute;left:960px;top:43px;display:flex;align-items:center;gap:14px;color:var(--navy);font-size:14px}
.power{width:24px;height:24px;border-radius:50%;background:var(--navy);display:flex;align-items:center;justify-content:center}
.btn{background:var(--navy);color:var(--white);border:none;border-radius:3px;font-family:inherit;display:flex;align-items:center;justify-content:center}
.back-btn{position:absolute;left:132px;top:123px;width:105px;height:27px;font-size:12px}
.side-nav{position:absolute;left:132px;top:166px;width:234px;height:422px;background:var(--white);border:1px solid var(--line);padding:0 13px}
.side-nav li{list-style:none;display:flex;align-items:center;gap:14px;font-size:13.5px;color:var(--text);border-bottom:1px solid var(--line);padding-left:11px}
.side-nav li:last-child{border-bottom:none}
.side-nav svg{width:14px;height:14px;fill:var(--navy);flex:none}
.form-panel{position:absolute;left:387px;top:166px;width:680px;height:750px;background:var(--white);border:1px solid var(--line)}
.form-title{position:absolute;left:21px;top:21px;font-size:13.5px;font-weight:600;color:var(--navy)}
.terms{position:absolute;left:21px;top:52px;width:648px;font-size:10.4px;line-height:19.2px;color:var(--muted)}
.terms p+p{margin-top:19.2px}
.abs{position:absolute}
.label-lg{font-size:14.5px;font-weight:700;color:var(--text)}
.label-sm{font-size:10.5px;color:var(--muted)}
.label-md{font-size:13px;color:var(--text)}
.field{position:absolute;background:var(--field);border:1px solid var(--field-border)}
.accept-btn{position:absolute;left:23px;top:439px;width:121px;height:26px;font-size:11px}
.payroll-title{position:absolute;left:0;width:100%;top:508px;text-align:center;font-size:14px;font-weight:600;color:var(--text)}
.payroll-box{position:absolute;left:23px;top:557px;width:633px;height:161px;border:1px solid #cccccc}
</style>
</head>
<body>
<header class="site-header">
  <div class="brand"><span class="brand-mark"></span><span class="brand-name">SENTINEL WATCH<br>SERVICES</span></div>
  <nav class="main-nav"><span>HOME</span><span class="sep">|</span><span class="help">HELP</span></nav>
  <div class="user"><span>Dana Reyes</span>
    <span class="power"><svg width="12" height="12" viewBox="0 0 12 12" fill="none" stroke="#fff" stroke-width="1.6" stroke-linecap="round"><path d="M3.6 3.2a4 4 0 1 0 4.8 0"/><path d="M6 1.2v4.2"/></svg></span>
  </div>
</header>

<button class="btn back-btn">Back To Profile</button>

<ul class="side-nav">
  <li style="height:64px"><svg viewBox="0 0 14 14"><rect x="0" y="3" width="14" height="8" rx="1"/><circle cx="7" cy="7" r="2" fill="#fff"/></svg>Direct Deposit</li>
  <li style="height:57px"><svg viewBox="0 0 14 14"><circle cx="7" cy="7" r="6"/></svg>Change W-4</li>
  <li style="height:56px"><svg viewBox="0 0 14 14"><rect x="1" y="2" width="12" height="10"/></svg>Labour Code</li>
  <li style="height:64px"><svg viewBox="0 0 14 14"><circle cx="7" cy="4" r="3"/><path d="M1 14a6 5 0 0 1 12 0z"/></svg>Personal Information</li>
  <li style="height:56px"><svg viewBox="0 0 14 14"><rect x="0" y="4" width="14" height="9" rx="1"/><rect x="4.5" y="1.5" width="5" height="3" fill="none" stroke="#1b1f6e" stroke-width="1.4"/></svg>Appraisal and Review</li>
  <li style="height:60px"><svg viewBox="0 0 14 14"><rect x="1" y="3" width="10" height="10" fill="none" stroke="#1b1f6e" stroke-width="1.5"/><path d="M6 9l1-3 6-6 2 2-6 6z"/></svg>Write Up-Slip</li>
  <li style="height:60px"><svg viewBox="0 0 14 14"><circle cx="7" cy="4" r="2.5"/><circle cx="2.5" cy="5" r="2"/><circle cx="11.5" cy="5" r="2"/><path d="M2 13a5 4 0 0 1 10 0z"/></svg>Employee Performance</li>
</ul>

<main class="form-panel">
  <h1 class="form-title">IMPORTANT! Please read and sign before completing and submitting.</h1>
  <div class="terms">
    <p>I hereby authorize SENTINEL WATCH SERVICES to deposit any amounts owed me, as instructed by my employer, by initiating credit entries to my account at the financial institution (hereinafter "Bank") indicated on this form. Further. I authorize Bank to accept and to credit any credit entries indicated by SENTINEL WATCH SERVICES to my account. In the even that SENTINEL WATCH SERVICES deposits funds erroneously into my account. I authorize SENTINEL WATCH SERVICES to debit my account for an amount not to exceed the original amount of the erroneous credit.</p>
    <p>This authorization is to remain in full force and effect until SENTINEL WATCH SERVICES and Bank have received written notice from me of its termination in such time and in such manner as to afford SENTINEL WATCH SERVICES and Bank reasonable opportunity to act on it.</p>
  </div>

  <div class="abs label-lg" style="left:23px;top:252px">Employee Name:</div>
  <div class="abs label-sm" style="left:23px;top:281px">Employee Signature</div>
  <div class="field" style="left:23px;top:315px;width:196px;height:22px"></div>
  <div class="field" style="left:23px;top:349px;width:196px;height:73px"></div>
  <div class="abs label-sm" style="left:325px;top:331px">Sign Date</div>
  <div class="field" style="left:379px;top:327px;width:196px;height:22px"></div>
  <button class="btn accept-btn">Accept Document</button>

  <h2 class="payroll-title">ONLY PAYROLL MANAGER SIGNS BELOW</h2>
  <section class="payroll-box">
    <div class="abs label-md" style="left:22px;top:11px">Company Name:</div>
    <div class="field" style="left:21px;top:39px;width:295px;height:22px"></div>
    <div class="abs label-md" style="left:22px;top:83px">Employee File Number:</div>
    <div class="field" style="left:21px;top:111px;width:175px;height:22px"></div>
    <div class="abs label-md" style="left:350px;top:11px">Comments:</div>
    <div class="field" style="left:349px;top:39px;width:262px;height:67px"></div>
  </section>
</main>
</body>
</html>
```